Business Card Design

Business Card for professional consulting firm working with large financial institutions.

Target Market(s)

Executive buyers

Industry/Entity Type

Banking

Contact Information for Business Card

Mild creativity wanted. Not boring, but do elaborate artwork.

Font styles to use
Serif
Sans Serif

Colors

Designer to choose colors to be used in the design.

Requirements
Must have
• Standard business card features - company name, individual name, telephone, website, email, locations.
Nice to have
• Two colors
Should not have
• too many colors, fancy printing, cartoons.

```html
<!DOCTYPE html>
<html lang="en">
<head>
<meta charset="utf-8">
<title>q5advisory — Business Card</title>
<link rel="stylesheet" href="https://fonts.googleapis.com/css2?family=Merriweather:wght@400&family=Roboto:wght@400&family=Roboto+Condensed:wght@500&display=swap">
<style>
  :root {
    --backdrop: #e8e4de;
    --card-white: #f3f3f3;
    --band-grey: #a9a9a9;
    --panel-black: #000000;
    --ink-dark: #1e1e1e;
    --text-white: #ffffff;
    --text-grey: #9a9a9a;
    --shadow: rgba(0, 0, 0, 0.28);
  }
  * { margin: 0; padding: 0; box-sizing: border-box; }
  html, body {
    width: 1200px;
    height: 960px;
    overflow: hidden;
    background: var(--backdrop);
  }
  .canvas {
    position: relative;
    width: 1200px;
    height: 960px;
  }
  .card {
    position: absolute;
    width: 600px;
    height: 343px;
    background: var(--card-white);
    box-shadow: 2px 3px 6px var(--shadow);
    overflow: hidden;
  }
  .card--front { left: 314px; top: 113px; }
  .card--back  { left: 312px; top: 472px; }

  .brand-name {
    position: absolute;
    left: 0;
    width: 100%;
    text-align: center;
    font-family: "Merriweather", serif;
    font-weight: 400;
    font-size: 34px;
    color: var(--ink-dark);
    letter-spacing: 0.5px;
  }
  .card--front .brand-name { top: 52px; }
  .card--back .brand-name  { top: 142px; }

  .accent-band {
    position: absolute;
    left: 0;
    top: 157px;
    width: 100%;
    height: 28px;
    background: var(--band-grey);
  }
  .info-panel {
    position: absolute;
    left: 0;
    top: 185px;
    width: 100%;
    height: 158px;
    background: var(--panel-black);
  }
  .panel-pointer {
    position: absolute;
    left: 84px;
    top: 185px;
  }
  .person {
    position: absolute;
    left: 45px;
    top: 240px;
    width: 128px;
    text-align: center;
  }
  .person__name {
    font-family: "Roboto Condensed", sans-serif;
    font-weight: 500;
    font-size: 23px;
    color: var(--text-white);
    line-height: 1.1;
    white-space: nowrap;
  }
  .person__title {
    font-family: "Roboto", sans-serif;
    font-size: 15px;
    color: var(--text-grey);
    margin-top: 3px;
    white-space: nowrap;
  }
  .contact {
    position: absolute;
    left: 349px;
    top: 213px;
    font-family: "Roboto", sans-serif;
    font-size: 14px;
    color: var(--text-white);
    line-height: 18px;
  }
  .contact__address { margin-bottom: 9px; }
  .contact__line {
    display: flex;
    align-items: center;
    gap: 8px;
    height: 19px;
  }
  .contact__icon { width: 13px; height: 13px; flex: none; }
</style>
</head>
<body>
<main class="canvas">

  <section class="card card--front" aria-label="Card front">
    <div class="brand-name">q5advisory</div>
    <div class="accent-band"></div>
    <div class="info-panel"></div>
    <svg class="panel-pointer" width="26" height="20" viewBox="0 0 26 20" aria-hidden="true">
      <polygon points="0,0 26,0 13,20" fill="var(--band-grey)"/>
    </svg>

    <div class="person">
      <div class="person__name">ALEX MORGAN</div>
      <div class="person__title">CEO/FOUNDER</div>
    </div>

    <div class="contact">
      <div class="contact__address">q5advisory 4120 Harbor View Road<br>Juneau, Alaska 99801</div>
      <div class="contact__line">
        <svg class="contact__icon" viewBox="0 0 16 16" aria-hidden="true">
          <path d="M3.5 1.5l2.5 0 1.2 3.2-1.6 1.2c.8 1.8 2.2 3.2 4 4l1.2-1.6 3.2 1.2 0 2.5c0 .8-.7 1.5-1.5 1.5C6.9 13.5 2 8.6 2 3c0-.8.7-1.5 1.5-1.5z" fill="var(--text-grey)"/>
        </svg>
        <span>555 014 2290</span>
      </div>
      <div class="contact__line">
        <svg class="contact__icon" viewBox="0 0 16 16" aria-hidden="true">
          <rect x="1" y="3" width="14" height="10" fill="var(--text-grey)"/>
          <polyline points="1,3 8,9 15,3" fill="none" stroke="var(--panel-black)" stroke-width="1.3"/>
        </svg>
        <span>info@q5advisory.com</span>
      </div>
      <div class="contact__line">
        <svg class="contact__icon" viewBox="0 0 16 16" aria-hidden="true">
          <circle cx="8" cy="8" r="7" fill="var(--text-grey)"/>
          <ellipse cx="8" cy="8" rx="3" ry="7" fill="none" stroke="var(--panel-black)" stroke-width="1"/>
          <line x1="1" y1="8" x2="15" y2="8" stroke="var(--panel-black)" stroke-width="1"/>
        </svg>
        <span>www.q5advisory.com</span>
      </div>
    </div>
  </section>

  <section class="card card--back" aria-label="Card back">
    <div class="brand-name">q5advisory</div>
  </section>

</main>
</body>
</html>
```